BRAMBLEFORD CONSTRUCTIONS B-Card

I currently have a b-card design but will be removing the image (tree) from the logo and have text only.
I want the card to be classy and strong within the building and construction industry.
I will be using Spot UV on the cards as per the attached examples. I will also send through some sketched ideas that I have in mind.
The color blue is similar to the image (No. 6) attached images

Target Market(s)

middle to maturre aged.
Home Owners / Renovators and Builders

Industry/Entity Type

Construction

Contact Information for Business Card

BRAMBLEFORD CONSTRUCTIONS
Name: Gareth Pennick
Title: Project Manager
Mobile: 0427 351 804
Office: (08) 9316 5172
Address: 47C Corvell Street, Malaga WA 6090
Email: info@bramblefordhomes.com.au
PO Box: 3817 Malaga WA 6944

Colors
0592cd
33a6d7
85cae6
1b1b1b

Requirements
Must have
• 1. It must have spot UV on the front of card, maybe back of card too
• 2. I really like the blue on image 6. (or at least a really cool electric blue against the charcoal grey background)
• 3. The font must be slimline and modern. Easy to read
• 4. There must be no black used on the card... Only greys and dark charcoal greys
• 5. Use only the text from the logo "Brambleford Constructions" Not the image of the tree. I am wanting the b-cards to be more masculine.
Nice to have
• 1. I like the design concept on image 6. but happy to see what else you can do with the Spot UV
• 2. Unless you have a really cool idea of the image of the tree (from previous logo) Spot UV somewhere in the design concept thats original and different then I am keen to see what you come up with
• 3. Try changing the color of the logo eg. full white or Blue and white
• 4. Another option is to have the Brambleford Logo on the front of card with the spot UV in the background of text which we specialise in eg, Roofing, Ceiling, Insulation, Gutter Guards, Electrical, Insurance etc and we can add or reduce items as required. Similar to image 12.
Should not have
• Do not include the image of the tree from previous logo. unless you have a really cool idea of Spot UV somewhere in the design concept thats original and different.

```html
<!DOCTYPE html>
<html lang="en">
<head>
<meta charset="utf-8">
<title>Brambleford Constructions – Business Card</title>
<link href="https://fonts.googleapis.com/css2?family=Jost:wght@400;500&display=swap" rel="stylesheet">
<style>
  :root {
    --backdrop: #3a3a3c;
    --card: #1b1b1d;
    --card-edge: #262629;
    --blue: #0592cd;
    --blue-deep: #1f6fc4;
    --white: #f2f2f2;
    --silver: #d4d4d6;
  }
  * { margin: 0; padding: 0; box-sizing: border-box; }
  html, body {
    width: 1200px; height: 747px; overflow: hidden;
    background: var(--backdrop);
    font-family: "Jost", "Futura", sans-serif;
  }
  .stage { position: relative; width: 1200px; height: 747px; }
  .card {
    position: absolute; width: 520px; height: 318px;
    background: var(--card);
    border: 1px solid var(--card-edge);
    border-radius: 18px;
    box-shadow: 0 18px 40px rgba(20,20,22,.55);
    overflow: hidden;
  }
  .card-front { left: 50px; top: 120px; }
  .card-back { left: 630px; top: 309px; }

  .company-name {
    font-weight: 500; font-style: normal; line-height: 1; white-space: nowrap;
  }
  .card-front .company-name {
    position: absolute; left: 0; right: 0; top: 124px;
    text-align: center; color: var(--silver); font-size: 30px;
  }
  .card-back .company-name {
    position: absolute; left: 34px; top: 40px;
    color: var(--blue); font-size: 24px;
  }

  .services {
    position: absolute; left: 0; right: 0; top: 198px;
    text-align: center; color: var(--white);
    font-size: 14px; font-weight: 400; line-height: 1.35; letter-spacing: .3px;
  }

  .address {
    position: absolute; left: 34px; top: 104px;
    color: var(--white); font-size: 15px; line-height: 1.3;
    font-style: normal;
  }
  .address .po { margin-top: 8px; }

  .contacts {
    position: absolute; left: 34px; top: 210px;
    list-style: none; color: var(--white); font-size: 15px; line-height: 1.4;
  }
  .contacts li { display: flex; align-items: center; gap: 9px; }
  .contacts svg { width: 13px; height: 13px; fill: var(--blue); flex: none; }

  .person { position: absolute; right: 44px; bottom: 40px; text-align: right; }
  .person-name { color: var(--blue-deep); font-size: 24px; font-weight: 500; line-height: 1.1; }
  .person-role { color: var(--white); font-size: 17px; line-height: 1.2; }

  .accent-bar {
    position: absolute; right: 16px; bottom: 30px;
    width: 12px; height: 38px; background: var(--blue-deep);
  }
</style>
</head>
<body>
<main class="stage">

  <section class="card card-front" aria-label="Business card front">
    <h1 class="company-name">BRAMBLEFORD CONSTRUCTIONS</h1>
    <p class="services">
      Roofing | Ceiling | Insulation | Gutter Guards<br>
      Electrical | Insurance etc
    </p>
  </section>

  <section class="card card-back" aria-label="Business card back">
    <h2 class="company-name">BRAMBLEFORD CONSTRUCTIONS</h2>

    <address class="address">
      <div>47C Corvell Street<br>Malaga WA 6090</div>
      <div class="po">PO Box:<br>3817 Malaga WA 6944</div>
    </address>

    <ul class="contacts">
      <li>
        <svg viewBox="0 0 24 24" aria-hidden="true"><path d="M6.6 10.8a15.1 15.1 0 0 0 6.6 6.6l2.2-2.2a1 1 0 0 1 1-.25 11.4 11.4 0 0 0 3.6.57 1 1 0 0 1 1 1V20a1 1 0 0 1-1 1A17 17 0 0 1 3 4a1 1 0 0 1 1-1h3.5a1 1 0 0 1 1 1c0 1.25.2 2.45.57 3.57a1 1 0 0 1-.25 1z"/></svg>
        (08) 9316 5172
      </li>
      <li>
        <svg viewBox="0 0 24 24" aria-hidden="true"><path d="M7 1h10a2 2 0 0 1 2 2v18a2 2 0 0 1-2 2H7a2 2 0 0 1-2-2V3a2 2 0 0 1 2-2zm0 3v14h10V4z"/></svg>
        0427 351 804
      </li>
      <li>
        <svg viewBox="0 0 24 24" aria-hidden="true"><path d="M2 5h20v14H2zm2 2v.5l8 5 8-5V7zm0 2.9V17h16V9.9l-8 5z"/></svg>
        info@bramblefordhomes.com.au
      </li>
    </ul>

    <div class="person">
      <p class="person-name">Gareth Pennick</p>
      <p class="person-role">Project Manager</p>
    </div>
    <span class="accent-bar" aria-hidden="true"></span>
  </section>

</main>
</body>
</html>
```